Need Business Card for eLearning Company

Need a business card designed for our company, CareerVantly.

CareerVantly has developed a complete 12 lesson eLearning course to teach you the skills you need to present yourself in a job interview. The course uses advanced learning techniques in the multimedia videos, plus contains quizzes and additional exercises to insure you get the course and can walk into any interview with confidence and ease, and get the job.

www.careervantly-example.com

Industry/Entity Type

Business

```html
<!DOCTYPE html>
<html lang="en">
<head>
<meta charset="utf-8">
<title>CareerVantly Business Card</title>
<link rel="stylesheet" href="https://fonts.googleapis.com/css2?family=Open+Sans:wght@400;600&family=Roboto+Condensed:wght@400;700&display=swap">
<style>
  :root {
    --backdrop: #ece9e4;
    --card: #ffffff;
    --card-shade: #f4f4f4;
    --plum: #8e1d7a;
    --leaf: #8dc63f;
    --ink: #3d3d3d;
    --ink-soft: #6b6b6b;
    --mark-grey: #4a4a4a;
    --fold: #e4e4e4;
  }
  * { margin: 0; padding: 0; box-sizing: border-box; }
  html, body {
    width: 1200px; height: 1024px; overflow: hidden;
    background: var(--backdrop);
  }
  .canvas { position: relative; width: 1200px; height: 1024px; }

  .card {
    position: absolute;
    width: 580px; height: 332px;
    background: linear-gradient(135deg, var(--card) 0%, var(--card-shade) 100%);
    box-shadow: 0 6px 18px rgba(0,0,0,0.12);
    overflow: hidden;
  }
  .card__band {
    position: absolute; left: 0; right: 0; bottom: 0;
    height: 22px; background: var(--plum);
  }

  .brand { position: absolute; display: flex; align-items: center; }
  .brand__square { background: var(--mark-grey); border-radius: 6px; flex: none; }
  .brand__name {
    font-family: "Open Sans", sans-serif; font-weight: 600;
    color: var(--ink); line-height: 1; white-space: nowrap;
  }

  /* Front */
  .card--front { left: 90px; top: 110px; }
  .card--front .fold-line {
    position: absolute; top: 0; bottom: 22px; left: 500px;
    width: 1px; background: var(--fold);
  }
  .card--front .brand { left: 70px; top: 118px; gap: 16px; }
  .card--front .brand__square { width: 44px; height: 44px; }
  .card--front .brand__name { font-size: 44px; }
  .card--front .site {
    position: absolute; left: 132px; top: 200px;
    font-family: "Open Sans", sans-serif; font-size: 13px;
    letter-spacing: 0.3em; color: var(--ink); white-space: nowrap;
  }

  /* Back */
  .card--back { left: 530px; top: 560px; }
  .card--back .brand { right: 34px; top: 36px; gap: 10px; }
  .card--back .brand__square { width: 26px; height: 26px; border-radius: 4px; }
  .card--back .brand__name { font-size: 26px; }
  .person { position: absolute; left: 34px; top: 118px; }
  .person__name {
    font-family: "Roboto Condensed", sans-serif; font-weight: 700;
    font-size: 26px; color: var(--ink);
  }
  .person__role {
    font-family: "Roboto Condensed", sans-serif; font-weight: 400;
    font-size: 16px; color: var(--plum); margin-top: 2px;
  }
  .contact { list-style: none; margin-top: 20px; }
  .contact__item {
    display: flex; align-items: center; gap: 10px;
    font-family: "Open Sans", sans-serif; font-size: 12.5px;
    color: var(--ink-soft); margin-bottom: 7px;
  }
  .contact__icon { width: 14px; height: 14px; flex: none; }
</style>
</head>
<body>
<main class="canvas">

  <section class="card card--front" aria-label="Business card front">
    <div class="fold-line"></div>
    <div class="brand">
      <span class="brand__square"></span>
      <span class="brand__name">CareerVantly</span>
    </div>
    <p class="site">WWW.CAREERVANTLY-EXAMPLE.COM</p>
    <div class="card__band"></div>
  </section>

  <section class="card card--back" aria-label="Business card back">
    <div class="brand">
      <span class="brand__name">CareerVantly</span>
      <span class="brand__square"></span>
    </div>
    <div class="person">
      <h1 class="person__name">Daniel R Whitford</h1>
      <p class="person__role">Managing Director</p>
      <ul class="contact">
        <li class="contact__item">
          <svg class="contact__icon" viewBox="0 0 14 14"><circle cx="7" cy="7" r="7" fill="#8dc63f"/><path d="M4.5 3.5l1.6 0.2 0.5 1.8-1 0.7a5 5 0 0 0 2.2 2.2l0.7-1 1.8 0.5 0.2 1.6c-3.6 0.6-6.6-2.4-6-6z" fill="#fff"/></svg>
          555-014-2291
        </li>
        <li class="contact__item">
          <svg class="contact__icon" viewBox="0 0 14 14"><circle cx="7" cy="7" r="7" fill="#8dc63f"/><rect x="3.5" y="4.5" width="7" height="5" fill="none" stroke="#fff" stroke-width="1"/><path d="M3.5 4.5L7 7.5l3.5-3" fill="none" stroke="#fff" stroke-width="1"/></svg>
          daniel@careervantly-example.com
        </li>
        <li class="contact__item">
          <svg class="contact__icon" viewBox="0 0 14 14"><circle cx="7" cy="7" r="7" fill="#8dc63f"/><circle cx="7" cy="7" r="3.5" fill="none" stroke="#fff" stroke-width="1"/><path d="M3.5 7h7M7 3.5v7" stroke="#fff" stroke-width="0.8"/></svg>
          www.careervantly-example.com
        </li>
      </ul>
    </div>
    <div class="card__band"></div>
  </section>

</main>
</body>
</html>
```